Need a business card design for a residential architect.

You can get a sense of his work at www.tberlove.com

Would like a consistent look and feel between business card and website
.

Target Market(s)

Residential homeowners builders

Industry/Entity Type

Residential

Contact Information for Business Card

Dale Morrick
Principle
Morrick Architecture
418 Kestrel Lane
Alder Grove, CA 95371

dale@tberlove.com

tberlove.com
phone: 650-555-2716
Fax: 650-555-8043

Font styles to use
Sans Serif

Requirements
Must have
• Details above
Nice to have
• Would like a consistent look and feel between business card and website
Should not have
• None

```html
<!DOCTYPE html>
<html lang="en">
<head>
<meta charset="utf-8">
<title>Morrick Architecture — Business Card</title>
<link rel="stylesheet" href="https://fonts.googleapis.com/css2?family=Open+Sans:wght@400;700&display=swap">
<style>
  :root {
    --backdrop: #3a2a26;
    --card-white: #ffffff;
    --ink: #111111;
    --brand-grey: #8a8a8a;
    --rule-grey: #9a9a9a;
    --silver-dark: #8e8e8e;
    --silver-light: #c4c4c4;
    --logo-white: #ffffff;
  }
  * { box-sizing: border-box; margin: 0; padding: 0; }
  html, body {
    width: 1200px; height: 1000px; overflow: hidden;
    background: var(--backdrop);
    font-family: "Open Sans", Arial, sans-serif;
  }
  .canvas { position: relative; width: 1200px; height: 1000px; }
  .card {
    position: absolute;
    width: 525px; height: 300px;
    box-shadow: 0 6px 18px rgba(0,0,0,0.45);
  }
  .card-front {
    left: 90px; top: 130px;
    background: var(--card-white);
    padding: 42px 44px;
    color: var(--ink);
  }
  .brand-name {
    font-weight: 400;
    color: var(--brand-grey);
    font-size: 25px;
    letter-spacing: 0.14em;
    text-transform: uppercase;
    line-height: 1;
    white-space: nowrap;
  }
  .brand-rule {
    width: 312px; height: 2px;
    background: var(--rule-grey);
    margin-top: 14px;
  }
  .person { margin-top: 26px; font-weight: 700; font-size: 19px; line-height: 1.4; }
  .details { margin-top: 22px; font-size: 15px; line-height: 1.45; }
  .website { margin-top: 8px; font-weight: 700; font-size: 17px; }
  .card-back {
    left: 585px; top: 500px;
    background: linear-gradient(115deg, var(--silver-dark) 0%, var(--silver-dark) 30%, var(--silver-light) 50%, var(--silver-dark) 70%, var(--silver-dark) 100%);
    display: flex; align-items: center; justify-content: center;
  }
  .card-back .brand-name {
    color: var(--logo-white);
    font-size: 28px;
  }
</style>
</head>
<body>
<main class="canvas">
  <section class="card card-front">
    <div class="brand-name">Morrick Architecture</div>
    <div class="brand-rule"></div>
    <div class="person">
      <div class="person-title">Dale Morrick Principle</div>
      <div class="person-phone">650-555-2716</div>
    </div>
    <div class="details">
      <div>418 Kestrel Lane Alder Grove, CA 95371</div>
      <div>email: dale@tberlove.com</div>
      <div>fax: 650-555-8043</div>
    </div>
    <div class="website">tberlove.com</div>
  </section>
  <section class="card card-back">
    <div class="brand-name">Morrick Architecture</div>
  </section>
</main>
</body>
</html>
```